Business Card Design - ChoiceCraft

Looking for creative, modern design, two sided for ChoiceCraft that is consistent with color and feel of website www.choicecraftpro.net.
Updates

Back of card will be used to promote products or have a quote revolving around decisions, change, leadership, innovation, creativity. Back should also have space to promote website, but optional to use the icon. Front of the card will need to use the icon and have standard place for name, job title, phone and email. We are not looking to put a mailing address or fax. Also want space to place a few words/phrase explaining what we do...such as individual growth and organizational development or tools, training, information...in addition, want the facebook icon small on the front somewhere as we are also on facebook.

Vector file uploaded of icon.

Target Market(s)

Professional coaching for individual growth and organizational development

Industry/Entity Type

Business

Requirements
Must have
• Icon...see attached.

```html
<!DOCTYPE html>
<html lang="en">
<head>
<meta charset="utf-8">
<title>ChoiceCraft Business Card</title>
<link href="https://fonts.googleapis.com/css2?family=Arimo:wght@400;700&family=Tinos:wght@400;700&display=swap" rel="stylesheet">
<style>
  :root {
    --stage: #d9dcdf;
    --card: #ffffff;
    --card-edge: #c9cdd1;
    --brand: #1a7cc1;
    --brand-deep: #0c5fa3;
    --brand-light: #5fb4e6;
    --ink: #222222;
    --muted: #555555;
    --mark: #9fc9ea;
  }
  * { margin: 0; padding: 0; box-sizing: border-box; }
  html, body { width: 1200px; height: 380px; overflow: hidden; background: var(--stage); }
  .canvas { position: relative; width: 1200px; height: 380px; }
  .card {
    position: absolute; background: var(--card);
    border: 1px solid var(--card-edge);
    box-shadow: 0 2px 6px rgba(0,0,0,.18);
  }
  .card--front { left: 55px; top: 42px; width: 525px; height: 300px; }
  .card--back { left: 625px; top: 38px; width: 523px; height: 300px; }

  .brand-mark {
    position: absolute; border-radius: 50%;
    background: radial-gradient(circle at 40% 35%, #e9f3fb, var(--mark) 60%, var(--brand) 100%);
  }
  .card--front .brand-mark { left: 113px; top: 30px; width: 110px; height: 110px; }
  .brand-name {
    position: absolute; left: 230px; top: 64px;
    font: 700 27px "Tinos", serif; color: var(--brand);
  }
  .tagline {
    position: absolute; left: 0; right: 0; top: 163px; text-align: center;
    font: 400 14px "Arimo", sans-serif; color: var(--ink);
  }
  .name-band {
    position: absolute; left: 0; right: 0; top: 187px; height: 44px;
    border-top: 2px solid var(--brand-light); border-bottom: 2px solid var(--brand-light);
    padding: 3px 0;
  }
  .name-band__bar {
    height: 100%;
    background: linear-gradient(90deg, var(--brand-deep), var(--brand) 40%, var(--brand-light) 75%, var(--brand));
    display: flex; align-items: center; justify-content: center;
    color: #fff; font: 400 15px "Tinos", serif;
  }
  .name-band__bar strong { font-weight: 700; font-size: 18px; margin-right: 4px; }
  .phone {
    position: absolute; left: 0; right: 0; top: 244px; text-align: center;
    font: 400 14px "Tinos", serif; color: var(--ink);
  }
  .contacts {
    position: absolute; left: 0; right: 0; top: 266px;
    display: flex; justify-content: center; gap: 10px;
    font: 400 14px "Tinos", serif; color: var(--ink);
  }
  .contacts span { display: inline-flex; align-items: center; gap: 5px; }
  .icon { width: 11px; height: 11px; fill: var(--muted); }
  .social-square { width: 10px; height: 10px; background: var(--brand-deep); display: inline-block; }

  .quote { position: absolute; left: 28px; display: flex; }
  .quote__dot {
    width: 20px; height: 20px; border-radius: 50%; margin-top: 2px;
    background: radial-gradient(circle at 40% 35%, #e9f3fb, var(--mark) 60%, var(--brand) 100%);
  }
  .quote__body { margin-left: 8px; }
  .quote__text {
    font: 400 13.5px "Arimo", sans-serif; color: var(--ink);
  }
  .quote__text::before { content: "\201C"; font: 700 26px "Tinos", serif; vertical-align: -9px; margin-right: 3px; }
  .quote__text::after { content: "\201D"; font: 700 26px "Tinos", serif; vertical-align: -14px; margin-left: 2px; }
  .quote__author {
    font: 700 13.5px "Arimo", sans-serif; color: var(--brand); margin-left: 14px; margin-top: 1px;
  }
  .quote__author::before { content: "- "; color: var(--ink); font-weight: 400; }
  .card--back .brand-mark { left: 385px; top: 170px; width: 96px; height: 96px; }
  .back-name {
    position: absolute; left: 378px; top: 270px; width: 110px; text-align: center;
    font: 700 14px "Tinos", serif; color: var(--brand);
  }
</style>
</head>
<body>
<div class="canvas">
  <section class="card card--front">
    <div class="brand-mark" role="img" aria-label="ChoiceCraft emblem area"></div>
    <div class="brand-name">ChoiceCraft</div>
    <p class="tagline">Supporting individual growth and&nbsp; organizational development.</p>
    <div class="name-band"><div class="name-band__bar"><strong>Your Name,</strong> Title</div></div>
    <p class="phone">&#9990; 123-456-789</p>
    <div class="contacts">
      <span><svg class="icon" viewBox="0 0 12 12"><path d="M0 3h12v8H0z M0 3l6 4 6-4" fill="none" stroke="#555" stroke-width="1.4"/></svg>hello@choicecraftpro.net</span>
      <span><svg class="icon" viewBox="0 0 12 12"><circle cx="6" cy="6" r="5" fill="none" stroke="#555" stroke-width="1.3"/><path d="M1 6h10M6 1c-3 3-3 7 0 10M6 1c3 3 3 7 0 10" fill="none" stroke="#555" stroke-width="1"/></svg>www.choicecraftpro.net</span>
      <span><i class="social-square"></i>/choicecraftpro</span>
    </div>
  </section>

  <section class="card card--back">
    <div class="quote" style="top:22px"><i class="quote__dot"></i><div class="quote__body"><p class="quote__text">Try not to become a man of success, but rather a man of value.</p><p class="quote__author">Arden Whitlow</p></div></div>
    <div class="quote" style="top:77px"><i class="quote__dot"></i><div class="quote__body"><p class="quote__text">The only constant is change.</p><p class="quote__author">Theron Vale</p></div></div>
    <div class="quote" style="top:130px"><i class="quote__dot"></i><div class="quote__body"><p class="quote__text">We are what we repeatedly do. Excellence is not an act, it is a habit.</p><p class="quote__author">Cassius Morrow</p></div></div>
    <div class="quote" style="top:182px"><i class="quote__dot"></i><div class="quote__body"><p class="quote__text">Simplicity is the ultimate sophistication.</p><p class="quote__author">Lorenzo Fabiani</p></div></div>
    <div class="quote" style="top:235px"><i class="quote__dot"></i><div class="quote__body"><p class="quote__text">Life is not fair - get used to it.</p><p class="quote__author">Wesley Harlan</p></div></div>
    <div class="brand-mark" role="img" aria-label="ChoiceCraft emblem area"></div>
    <div class="back-name">ChoiceCraft</div>
  </section>
</div>
</body>
</html>
```